Quillmarsh Property Solutions need a business card design

Hello guys. We would need a business card design asap please.
We are a start up property investment business based in London UK specialised in buying, selling, managing and letting properties and helping distressed property owners.
The name of our Business is Quillmarsh, the logo symbolises the four fundamental elements of the world (earth, air, fire and water) and so it stands for strength, stability, longevity.
We would like the business card to communicate professionalism and reliability. Many many thanks indeed for your work.

Details:

1.) Rosalind Updike
Property Investor
Mobile: +44(0)7700123456
Email: rosalind.quillmarsh@mailbox-example.com

2.) Dominic Updike
Property Investor
Mobile: +44(0)7700987654
Email: dominic.quillmarsh@mailbox-example.com

```html
<!DOCTYPE html>
<html lang="en">
<head>
<meta charset="utf-8">
<title>Quillmarsh Property Solutions – Business Card</title>
<link href="https://fonts.googleapis.com/css2?family=Josefin+Sans:wght@600;700&family=Open+Sans:wght@400;600&display=swap" rel="stylesheet">
<style>
  :root {
    --backdrop: #e9e6e2;
    --card: #ffffff;
    --card-edge: #2a2a2a;
    --wordmark: #9a9a9a;
    --name-blue: #3a6cb4;
    --body-text: #3c3c3c;
    --icon-blue: #3a6cb4;
    --mark-red: #d8262e;
  }
  * { margin: 0; padding: 0; box-sizing: border-box; }
  html, body {
    width: 1200px; height: 377px; overflow: hidden;
    background: var(--backdrop);
  }
  .canvas { position: relative; width: 1200px; height: 377px; }
  .card {
    position: absolute; top: 25px; height: 322px;
    background: var(--card);
    border: 1.5px solid var(--card-edge);
    overflow: hidden;
    font-family: "Open Sans", Arial, sans-serif;
    color: var(--body-text);
  }
  .card--front { left: 34px; width: 556px; }
  .card--back { left: 599px; width: 560px; }

  .brand-mark {
    position: absolute; left: 44px; top: 56px;
    display: flex; align-items: center; gap: 10px;
    font-family: "Josefin Sans", Arial, sans-serif;
    font-weight: 700; font-size: 22px; line-height: 24px; color: var(--mark-red);
  }
  .brand-mark__square { width: 16px; height: 16px; background: var(--mark-red); }

  .wordmark {
    position: absolute; text-align: center; white-space: nowrap;
    font-family: "Josefin Sans", Arial, sans-serif; color: var(--wordmark);
  }
  .wordmark__name { font-weight: 700; text-transform: uppercase; letter-spacing: 0.04em; }
  .wordmark__tag { font-weight: 600; text-transform: uppercase; letter-spacing: 0.04em; }

  .card--front .wordmark { left: 14px; top: 150px; width: 186px; }
  .card--front .wordmark__name { font-size: 20px; line-height: 24px; }
  .card--front .wordmark__tag { font-size: 11px; line-height: 14px; margin-top: 2px; }

  .contact__item { position: absolute; left: 26px; white-space: nowrap; }
  .contact__name { top: 209px; font-size: 17px; font-weight: 600; line-height: 24px; color: var(--name-blue); }
  .contact__role { top: 236px; font-size: 13px; line-height: 18px; }
  .contact__line { display: flex; align-items: center; gap: 8px; font-size: 13px; line-height: 18px; }
  .contact__line--phone { top: 265px; }
  .contact__line--email { top: 291px; }
  .contact__line svg { width: 11px; height: 12px; fill: var(--icon-blue); flex: none; }

  .card--back .wordmark { left: 206px; top: 229px; width: 340px; }
  .card--back .wordmark__name { font-size: 30px; line-height: 32px; }
  .card--back .wordmark__tag { font-size: 15px; line-height: 18px; margin-top: 6px; }
  .website {
    position: absolute; left: 206px; top: 285px; width: 340px;
    text-align: center; white-space: nowrap;
    font-size: 16px; line-height: 22px; letter-spacing: 0.06em; color: var(--body-text);
  }
</style>
</head>
<body>
<main class="canvas">
  <section class="card card--front" aria-label="Card front">
    <div class="brand-mark"><span class="brand-mark__square"></span>Quillmarsh</div>
    <div class="wordmark">
      <div class="wordmark__name">Quillmarsh</div>
      <div class="wordmark__tag">Property Solutions</div>
    </div>
    <div class="contact__item contact__name">Rosalind Updike</div>
    <div class="contact__item contact__role">Property Investor</div>
    <div class="contact__item contact__line contact__line--phone">
      <svg viewBox="0 0 11 12" aria-hidden="true"><rect x="2" y="0" width="7" height="12" rx="1.5"/><rect x="3.5" y="2" width="4" height="5" fill="#fff"/></svg>
      +44(0)7700123456
    </div>
    <div class="contact__item contact__line contact__line--email">
      <svg viewBox="0 0 11 12" aria-hidden="true"><rect x="0" y="3" width="11" height="8" rx="1"/><path d="M0.8 3.8 L5.5 7.5 L10.2 3.8" stroke="#fff" stroke-width="1" fill="none"/></svg>
      rosalind.quillmarsh@mailbox-example.com
    </div>
  </section>

  <section class="card card--back" aria-label="Card back">
    <div class="wordmark">
      <div class="wordmark__name">Quillmarsh</div>
      <div class="wordmark__tag">Property Solutions</div>
    </div>
    <div class="website">www.quillmarsh-example.com</div>
  </section>
</main>
</body>
</html>
```